How likely are people to engage in social distancing? We need a good illustration to show the data!

We surveyed U.S. adults March 20th - 24th, 2020 and asked how likely they were to engage in social distancing (and other COVID-19 related health behaviors). What did the survey find? Basically, most people intend to engage in social distancing behaviors (e.g., avoiding large crowds) and other behaviors that reduce the spread of COVID-19 (e.g., washing hands at least 20 seconds). When most people intend to engage in a behavior, then public health professionals try to leverage that to move more people to act.
Now we need innovative and professional images that attempt to communicate one or all of these findings. The specific findings are nicely summarized in the attached document. For example, 82% of participants intend to engage in social distancing.
What sort of visual are we looking for? Our preference is for an original illustration (or set of illustrations). Our preference is for (creative and powerful illustrations, but we are also open to the creative and well-executed infographics.
We need these images fast . We will award monetary prizes to the 3 best designs. If we like more than that, then we might purchase more (e.g., in past contests, we have purchased as many as 30 designs).
What we will need:
(1) The illustrations must be original and we will need the photoshop and/or illustrator files for all artwork.
(2) You can illustrate all of the findings or just one of them. We need creative approaches that do a lucid job of bringing the data to life. Most people intend to engage in these behaviors. How to communicate that? Republicans and Democrats do not differ in their intentions; how to communicate that?
(3) The illustration should say, somewhere: "Based on a survey of 400 U.S. adults conducted March 20 - 24th, 2020."

U.S. Adults

• Original illustrations based on the findings of the survey (see attached document).

```html
<!DOCTYPE html>
<html lang="en">
<head>
<meta charset="utf-8">
<title>Comparing Republicans and Democrats in Covid-19 Prevention</title>
<link rel="stylesheet" href="https://fonts.googleapis.com/css2?family=Open+Sans:wght@600;700;800&display=swap">
<style>
  :root {
    --teal: #00dcc0;
    --teal-line: #5ef0dc;
    --red: #f2212b;
    --red-deep: #c3121c;
    --blue: #1c0fd6;
    --navy: #0b1f7a;
    --magenta: #e6007e;
    --yellow: #ffe600;
    --ink: #1f1a2b;
    --white: #ffffff;
  }
  html, body { margin: 0; padding: 0; overflow: hidden; }
  body { width: 1200px; height: 863px; background: var(--teal); font-family: "Open Sans", sans-serif; }
  .poster { position: relative; width: 1200px; height: 863px; overflow: hidden; background: var(--teal); }

  .virus-field { position: absolute; left: 0; top: 0; width: 480px; height: 300px;
    background: radial-gradient(circle at 150px 110px, var(--teal-line) 0, rgba(94,240,220,0) 150px); opacity: .55; }

  .data-panel { position: absolute; inset: 0; width: 1200px; height: 863px; }

  .title { position: absolute; left: 0; top: 0; margin: 0; font-weight: 700; color: var(--white); }
  .title-line { position: absolute; left: 35px; font-size: 47px; line-height: 1; white-space: nowrap; text-shadow: 2px 3px 4px rgba(0,0,0,.25); }
  .title-line.comparing { top: 295px; }
  .title-band { position: absolute; left: 0; height: 76px; }
  .title-band.red { top: 357px; width: 363px; background: var(--red); clip-path: polygon(0 0, 335px 0, 100% 100%, 0 100%); }
  .title-band.blue { top: 499px; width: 348px; background: var(--navy); clip-path: polygon(0 0, 316px 0, 100% 100%, 0 100%); }
  .title-line.republicans { top: 367px; }
  .title-line.and { top: 437px; }
  .title-line.democrats { top: 509px; }
  .title-line.focus { font-size: 72px; font-weight: 800; color: var(--magenta); left: 33px; letter-spacing: -1px;
    text-shadow: 0 0 0 var(--white), 2px 2px 0 var(--white), -2px -2px 0 var(--white), 2px -2px 0 var(--white), -2px 2px 0 var(--white), 3px 5px 6px rgba(0,0,0,.3); }
  .title-line.focus.top { top: 600px; }
  .title-line.focus.bottom { top: 687px; }

  .source { position: absolute; left: 35px; top: 782px; margin: 0; font-size: 20.5px; line-height: 27px; font-weight: 700; color: var(--ink); }

  .party { position: absolute; top: 20px; width: 150px; text-align: center; color: var(--white); font-weight: 700; font-size: 22px; letter-spacing: .2px; }
  .party .mark { display: block; width: 54px; height: 54px; margin: 0 auto 12px; border-radius: 50%; background: var(--white); }
  .party.left { left: 511px; }
  .party.right { left: 1017px; }

  .question { position: absolute; left: 660px; top: 36px; width: 360px; margin: 0; text-align: center; font-size: 18.5px; line-height: 21.5px; font-weight: 700; color: var(--yellow); }
  .question .label { display: block; color: var(--white); }

  .rows { position: absolute; left: 0; top: 144px; width: 1200px; margin: 0; padding: 0; list-style: none; }
  .row { position: absolute; left: 520px; width: 680px; height: 80px; display: flex; align-items: center;
    background: linear-gradient(90deg, rgba(242,33,43,0) 0%, rgba(250,170,175,.85) 22%, var(--white) 48%, rgba(200,195,245,.9) 68%, rgba(28,15,214,0) 92%);
    box-shadow: 0 3px 0 rgba(160,10,30,.25); }
  .row .value { position: absolute; font-size: 56px; font-weight: 800; line-height: 1; color: var(--white); letter-spacing: -1px; text-shadow: 2px 3px 5px rgba(0,0,0,.3); }
  .row .value small { font-size: 30px; letter-spacing: 0; }
  .row .value.rep { left: 20px; }
  .row .value.dem { left: 514px; }
  .row .behaviour { position: absolute; left: 161px; width: 320px; text-align: center; font-size: 22.5px; line-height: 28px; font-weight: 700; color: var(--ink); }
</style>
</head>
<body>
<main class="poster">
  <div class="virus-field" role="img" aria-label="Faint outline illustrations of coronavirus particles"></div>

  <svg class="data-panel" viewBox="0 0 1200 863" aria-hidden="true">
    <defs>
      <linearGradient id="panelFill" x1="470" y1="0" x2="1200" y2="0" gradientUnits="userSpaceOnUse">
        <stop offset="0" stop-color="#c3121c"/>
        <stop offset="0.08" stop-color="#f2212b"/>
        <stop offset="0.45" stop-color="#e8202f"/>
        <stop offset="0.62" stop-color="#5a13a6"/>
        <stop offset="0.78" stop-color="#1c0fd6"/>
        <stop offset="1" stop-color="#1c0fd6"/>
      </linearGradient>
    </defs>
    <path fill="url(#panelFill)" d="M480 0 C500 70 440 160 445 260 C450 360 495 400 488 470 C480 560 440 600 455 680 C470 760 510 810 520 863 L1200 863 L1200 0 Z"/>
  </svg>

  <h1 class="title">
    <span class="title-line comparing">Comparing</span>
    <span class="title-band red"></span>
    <span class="title-line republicans">Republicans</span>
    <span class="title-line and">and</span>
    <span class="title-band blue"></span>
    <span class="title-line democrats">Democrats</span>
    <span class="title-line focus top">in Covid-19</span>
    <span class="title-line focus bottom">Prevention</span>
  </h1>

  <p class="source">Based on a survey of 400 U.S. adults<br>conducted March 20 - 24th, 2020</p>

  <div class="party left"><span class="mark"></span>REPUBLICANS</div>
  <p class="question"><span class="label">Question:</span>How likely it is that you will perform these behaviors to slow the spread of coronavirus?</p>
  <div class="party right"><span class="mark"></span>DEMOCRATS</div>

  <ul class="rows">
    <li class="row" style="top:0px"><span class="value rep">82<small>%</small></span><span class="behaviour">Engage in<br>social distancing</span><span class="value dem">81<small>%</small></span></li>
    <li class="row" style="top:90px"><span class="value rep">60<small>%</small></span><span class="behaviour">Work<br>from home</span><span class="value dem">65<small>%</small></span></li>
    <li class="row" style="top:180px"><span class="value rep">85<small>%</small></span><span class="behaviour">Avoid large<br>gatherings</span><span class="value dem">84<small>%</small></span></li>
    <li class="row" style="top:270px"><span class="value rep">82<small>%</small></span><span class="behaviour">Cancel<br>social activities</span><span class="value dem">80<small>%</small></span></li>
    <li class="row" style="top:359px"><span class="value rep">84<small>%</small></span><span class="behaviour">Put distance between<br>yourself and other people</span><span class="value dem">87<small>%</small></span></li>
    <li class="row" style="top:449px"><span class="value rep">87<small>%</small></span><span class="behaviour">Wash hands<br>at least 20 seconds</span><span class="value dem">88<small>%</small></span></li>
    <li class="row" style="top:539px"><span class="value rep">87<small>%</small></span><span class="behaviour">Use<br>hand sanitizer</span><span class="value dem">84<small>%</small></span></li>
    <li class="row" style="top:628px"><span class="value rep">80<small>%</small></span><span class="behaviour">Avoid touching your eyes,<br>nose, and mouth</span><span class="value dem">82<small>%</small></span></li>
  </ul>
</main>
</body>
</html>
```